Sea Shipping Logistics Company

The business is a logistics company (sea shipping and other special logistics) and also sales of bulk building materials.
The Design should be minimalistic and give a feeling of power and connectivity.
When the client sees the card, they should get a feeling of confident. Dark overall color (background) and print should be red / white .See logo. The card will be printed on trifecta with the middle color being red.

One side should be the logo and a 5 / 6 word slogan
And other side name, contact (phone/email) and a QR Code.

Target Market(s)

Construction companies / Oil & Gas related companies

Industry/Entity Type

Sea Bulk Shipping Logistics

Contact Information for Business Card

Name, Telephone number, Email address, Website URL, QR Code (see description)

Font styles to use
Sans Serif

Requirements
Must have
• No idea
Nice to have
• Minimalistic, but strong and powerful look and feel.

```html
<!DOCTYPE html>
<html lang="en">
<head>
<meta charset="utf-8">
<title>Korven Business Card</title>
<link href="https://fonts.googleapis.com/css2?family=Archivo:wght@400;600;800&display=swap" rel="stylesheet">
<style>
  :root {
    --stage: #c4c4c4;
    --card: #1b1c1e;
    --red: #ee3a32;
    --white: #ffffff;
    --grey: #e6e6e6;
  }
  * { margin: 0; padding: 0; box-sizing: border-box; }
  html, body { width: 1200px; height: 800px; overflow: hidden; }
  body {
    background: var(--stage);
    font-family: "Archivo", Arial, sans-serif;
    position: relative;
  }
  .card {
    position: absolute;
    top: 250px;
    width: 525px;
    height: 300px;
    background: var(--card);
    border-radius: 16px;
    border: 2px solid var(--red);
    overflow: hidden;
    box-shadow: 0 18px 30px rgba(0,0,0,0.25);
  }
  .card--contact { left: 45px; }
  .card--brand { left: 630px; }

  /* contact side */
  .edge-block {
    position: absolute;
    right: 0; top: 34px;
    width: 34px; height: 66px;
    background: var(--red);
  }
  .identity {
    position: absolute;
    left: 34px; top: 98px;
  }
  .identity__name {
    color: var(--red);
    font-weight: 800;
    font-size: 22px;
    letter-spacing: 0.5px;
    text-transform: uppercase;
  }
  .identity__role {
    color: var(--white);
    font-size: 12px;
    letter-spacing: 1px;
    text-transform: uppercase;
    margin-top: 2px;
  }
  .contact-band {
    position: absolute;
    left: 0; top: 168px;
    width: 300px; height: 96px;
    background: var(--red);
    padding: 14px 0 0 34px;
  }
  .contact-band__line {
    display: flex;
    align-items: center;
    gap: 8px;
    color: var(--white);
    font-size: 14px;
    font-weight: 600;
    line-height: 22px;
    white-space: nowrap;
  }
  .contact-band__line svg { width: 14px; height: 14px; flex: none; }
  .mark-frame {
    position: absolute;
    right: 62px; top: 62px;
    width: 150px; height: 150px;
    border: 3px solid var(--grey);
    display: flex;
    align-items: center;
    justify-content: center;
  }
  .mark-frame__name {
    color: var(--white);
    font-weight: 800;
    font-size: 26px;
    letter-spacing: 1px;
  }

  /* brand side */
  .brand {
    position: absolute;
    left: 50%; top: 50%;
    transform: translate(-50%, -50%);
    display: flex;
    align-items: center;
    gap: 18px;
  }
  .brand__square {
    width: 92px; height: 92px;
    border: 3px solid var(--grey);
    flex: none;
  }
  .brand__name {
    color: var(--white);
    font-weight: 800;
    font-size: 62px;
    line-height: 1;
    letter-spacing: 1px;
  }
  .brand__tagline {
    color: var(--white);
    font-size: 14px;
    letter-spacing: 1.5px;
    text-transform: uppercase;
    margin-top: 6px;
    white-space: nowrap;
  }
</style>
</head>
<body>

<section class="card card--contact">
  <div class="edge-block"></div>
  <div class="identity">
    <p class="identity__name">Marcus Hale</p>
    <p class="identity__role">Managing Director</p>
  </div>
  <div class="contact-band">
    <p class="contact-band__line">
      <svg viewBox="0 0 16 16" aria-hidden="true"><path fill="#fff" d="M3.6 1.5l2.3 2.6-1.3 1.7c.9 2 2.5 3.6 4.6 4.6l1.7-1.3 2.6 2.3-1.4 2.3C6.5 13.4 2.6 9.5 1.3 3.1z"/></svg>
      055-210 384 617
    </p>
    <p class="contact-band__line">
      <svg viewBox="0 0 16 16" aria-hidden="true"><rect x="1" y="3" width="14" height="10" fill="#fff"/><path d="M1 3l7 6 7-6" fill="none" stroke="#ee3a32" stroke-width="1.5"/></svg>
      hello@korvenfreight.com
    </p>
    <p class="contact-band__line">
      <svg viewBox="0 0 16 16" aria-hidden="true"><circle cx="8" cy="8" r="7" fill="#fff"/><path d="M1 8h14M8 1v14M3 4.5h10M3 11.5h10" stroke="#ee3a32" stroke-width="1"/><ellipse cx="8" cy="8" rx="3" ry="7" fill="none" stroke="#ee3a32" stroke-width="1"/></svg>
      www.korvenfreight.com
    </p>
  </div>
  <div class="mark-frame">
    <span class="mark-frame__name">KORVEN</span>
  </div>
</section>

<section class="card card--brand">
  <div class="brand">
    <div class="brand__square"></div>
    <div class="brand__text">
      <p class="brand__name">KORVEN</p>
      <p class="brand__tagline">Transport &amp; Freight</p>
    </div>
  </div>
</section>

</body>
</html>
```